Whitcombe Business Card Design

The name of the business is Dario Whitcombe, CPA LLC
The service that we offer is Accounting, Tax & Consulting Services. I need it to have the following items:
Dario Whitcombe, Principal
Phone Number
Email Address
Physical Address

I have attached the company logo, one in black and one in white. Please provide a design in black background and the other in white background. Please include "Accounting, Tax & Consulting Services". I want the business card to be clean and very professional.

```html
<!DOCTYPE html>
<html lang="en">
<head>
<meta charset="utf-8">
<title>Dario Whitcombe, CPA LLC – Business Cards</title>
<link rel="stylesheet" href="https://fonts.googleapis.com/css2?family=Montserrat:wght@500;600;700&family=Roboto:wght@300;400&display=swap">
<style>
  :root {
    --backdrop: #2a2a2a;
    --card: #ededed;
    --card-shade: #e2e2e2;
    --ink: #333436;
    --muted: #7b7c7e;
    --accent: #8e1518;
    --rule: #8a8b8d;
    --band-grey: #8d8e90;
  }
  * { margin: 0; padding: 0; box-sizing: border-box; }
  html, body { width: 1200px; height: 1138px; overflow: hidden; }
  body {
    background: var(--backdrop);
    position: relative;
    font-family: "Roboto", sans-serif;
    color: var(--ink);
  }
  .card {
    position: absolute;
    background: linear-gradient(160deg, #f3f3f3 0%, var(--card) 55%, var(--card-shade) 100%);
    border-radius: 16px;
    overflow: hidden;
  }
  .card--front { left: 272px; top: 184px; width: 622px; height: 376px; }
  .card--back  { left: 274px; top: 606px; width: 619px; height: 375px; }

  .brand-name {
    font-family: "Montserrat", sans-serif;
    font-weight: 600;
    color: var(--ink);
    white-space: nowrap;
  }
  .brand-tagline {
    font-family: "Montserrat", sans-serif;
    font-weight: 600;
    color: var(--muted);
    letter-spacing: 0.12em;
    white-space: nowrap;
  }
  .brand-square { position: absolute; background: var(--ink); }

  /* Front */
  .card--front .brand-square { left: 281px; top: 112px; width: 60px; height: 60px; }
  .card--front .brand-name { position: absolute; left: 0; right: 0; top: 200px; text-align: center; font-size: 25px; }
  .card--front .brand-tagline { position: absolute; left: 0; right: 0; top: 236px; text-align: center; font-size: 17px; }
  .services { position: absolute; left: 0; right: 0; top: 327px; text-align: center; font-size: 16px; color: #222; }
  .band { position: absolute; bottom: 0; height: 9px; }
  .band--accent { left: 0; width: 50%; background: var(--accent); }
  .band--grey { right: 0; width: 50%; background: var(--band-grey); }

  /* Back */
  .card--back .brand-square { left: 30px; top: 44px; width: 72px; height: 72px; }
  .card--back .brand-name { position: absolute; left: 118px; top: 52px; font-size: 24px; }
  .card--back .brand-tagline { position: absolute; left: 118px; top: 87px; font-size: 17px; }
  .person { position: absolute; left: 30px; top: 208px; }
  .person-name { font-family: "Montserrat", sans-serif; font-weight: 700; font-size: 21px; color: var(--accent); letter-spacing: 0.02em; }
  .person-role { font-size: 16px; font-weight: 300; color: var(--ink); margin-top: 1px; }
  .divider { position: absolute; left: 0; top: 0; }
  .address { position: absolute; left: 30px; top: 298px; font-size: 16px; font-weight: 300; line-height: 24px; color: var(--ink); }
  .contact { position: absolute; right: 28px; top: 278px; list-style: none; }
  .contact li { display: flex; align-items: center; justify-content: flex-end; height: 24px; font-size: 16px; font-weight: 300; }
  .contact svg { width: 15px; height: 15px; margin-left: 12px; fill: var(--accent); }
</style>
</head>
<body>
  <section class="card card--front">
    <div class="brand-square"></div>
    <div class="brand-name">DARIO WHITCOMBE, CPA LLC</div>
    <div class="brand-tagline">CERTIFIED PUBLIC ACCOUNTANT</div>
    <p class="services">Accounting, Tax &amp; Consulting Services</p>
    <div class="band band--accent"></div>
    <div class="band band--grey"></div>
  </section>

  <section class="card card--back">
    <div class="brand-square"></div>
    <div class="brand-name">DARIO WHITCOMBE, CPA LLC</div>
    <div class="brand-tagline">CERTIFIED PUBLIC ACCOUNTANT</div>

    <div class="person">
      <div class="person-name">DARIO WHITCOMBE</div>
      <div class="person-role">Principal</div>
    </div>

    <svg class="divider" width="619" height="375" viewBox="0 0 619 375">
      <path d="M30 276 H310 C345 276 345 251 380 251 H590" fill="none" stroke="var(--rule)" stroke-width="2"/>
    </svg>

    <p class="address">4821 Larkspur Avenue, Suite 2,<br>Asheville, NC 28801</p>

    <ul class="contact">
      <li>828-555-0142
        <svg viewBox="0 0 16 16"><path d="M2 6 C2 3 14 3 14 6 L12 7 L11 5.5 H5 L4 7 Z M4 8 H12 L13 13 H3 Z"/></svg>
      </li>
      <li>dw@dariowhitcombellc.com
        <svg viewBox="0 0 16 16"><path d="M1 3 H15 V13 H1 Z M2.5 4.5 L8 9 L13.5 4.5 Z" fill-rule="evenodd"/></svg>
      </li>
      <li>www.dariowhitcombellc.com
        <svg viewBox="0 0 16 16"><circle cx="8" cy="8" r="7"/><path d="M1 8 H15 M8 1 V15 M8 1 C4 5 4 11 8 15 M8 1 C12 5 12 11 8 15" stroke="#ededed" stroke-width="1" fill="none"/></svg>
      </li>
    </ul>
  </section>
</body>
</html>
```